Business Card Design

We need a design for business cards for our company. We have a logo. We teach EMT's and we are based out of Virginia. The information that will need to add would be, name, title, phone number, email, address. On the back of the business card would be "We help you, help others"

Target Market(s)

People that want to become EMT's

Colors

Designer to choose colors to be used in the design.

Requirements
Must have
• company logo

```html
<!DOCTYPE html>
<html lang="en">
<head>
<meta charset="utf-8">
<title>Medic Path Academy – Business Card</title>
<link rel="stylesheet" href="https://fonts.googleapis.com/css2?family=Lato:wght@400;700&display=swap">
<style>
  :root {
    --backdrop: #6b6b6b;
    --card-light: #ffffff;
    --card-dark: #1f2a33;
    --brand-red: #c0161f;
    --tag-red: #d8222c;
    --text-grey: #4a4a4a;
    --tag-grey: #b9bec3;
  }
  * { margin: 0; padding: 0; box-sizing: border-box; }
  html, body { width: 1200px; height: 900px; overflow: hidden; }
  body {
    background: var(--backdrop);
    font-family: "Lato", Arial, sans-serif;
    position: relative;
  }
  .card {
    position: absolute;
    top: 200px;
    width: 310px;
    height: 502px;
  }
  .card-front {
    left: 253px;
    background: var(--card-light);
    border-radius: 62px 0 62px 0;
  }
  .card-back {
    left: 627px;
    background: var(--card-dark);
    border-radius: 0 62px 0 62px;
  }
  .brand {
    position: absolute;
    left: 0; right: 0;
    display: flex;
    align-items: center;
    justify-content: center;
    gap: 8px;
    font-weight: 700;
    font-size: 19px;
    letter-spacing: 0.5px;
    color: var(--brand-red);
    text-transform: uppercase;
  }
  .brand-mark {
    width: 14px; height: 14px;
    background: var(--brand-red);
  }
  .card-front .brand { top: 144px; }
  .card-back .brand { top: 228px; }
  .holder {
    position: absolute;
    left: 34px;
    top: 320px;
    color: var(--text-grey);
  }
  .holder-name {
    font-size: 19px;
    font-weight: 700;
    color: var(--brand-red);
    text-transform: uppercase;
    line-height: 1;
  }
  .holder-title { font-size: 15px; margin-top: 1px; line-height: 18px; }
  .contact { list-style: none; margin-top: 10px; font-size: 15px; }
  .contact li { display: flex; align-items: center; gap: 4px; height: 18px; }
  .contact svg { width: 14px; height: 12px; fill: var(--brand-red); }
  .address { font-size: 15px; margin-top: 10px; line-height: 18px; }
  .tagline {
    position: absolute;
    left: 0; right: 0;
    top: 433px;
    text-align: center;
    font-size: 15px;
    font-weight: 700;
    text-transform: uppercase;
    color: var(--tag-grey);
  }
  .tagline-lead { color: var(--tag-red); }
</style>
</head>
<body>
  <section class="card card-front">
    <div class="brand"><span class="brand-mark"></span>Medic Path Academy</div>
    <div class="holder">
      <p class="holder-name">Daniel Reyes</p>
      <p class="holder-title">Managing Director</p>
      <ul class="contact">
        <li>
          <svg viewBox="0 0 14 12" aria-hidden="true"><path d="M1 4c0-2 3-3 6-3s6 1 6 3v1h-3V4H4v1H1zM3 6h8l2 5H1z"/></svg>
          044-987 650 312
        </li>
        <li>
          <svg viewBox="0 0 14 12" aria-hidden="true"><path d="M1 2h12v8H1z M1 2l6 5 6-5" stroke="#fff" stroke-width="1"/></svg>
          info@medicpath.com
        </li>
      </ul>
      <p class="address">421, Address line goes here<br>45452,Country Name</p>
    </div>
  </section>

  <section class="card card-back">
    <div class="brand"><span class="brand-mark"></span>Medic Path Academy</div>
    <p class="tagline"><span class="tagline-lead">We help you,</span> help others</p>
  </section>
</body>
</html>
```